Banner Ad Design Project

We need a 728x90 and a 300x250
1st option
"I have a lead for you. Click here to close the deal."
In large bold letters.
Under this in smaller letters,
"Lornavel. For serious business networkers"
2nd option
"Put that coffee down!"
"Coffee's for closers only."
Close more deals. LORNAVEL LOGO
(this is a quote from Harrowmere Tide. It is a famous sales movie)
The other option is
"First you get the money" "Then you get the power" in bold letters.
"Lornavel. For serious business networkers" in smaller letters at the bottom.
-Must have our colors
-Must have our logo (Small at the bottom right)
-Watch the video at lornavel () com
Please be creative. If the banner can have multiple images that would be great as well.
This needs to be a serious looking ad that is bold and clean.
Updates
Please be sure to use the phrase, "Put that coffee down! Coffee's for closers only" with the logo and at the bottom the words, Lornavel, for serious business networkers. in one of the designs. This will be our first campaign. I am looking for a very simple design that is bold. Perhaps just a coffee cup with the words and no other graphics.
Target Market(s)
Sales professionals
Industry/Entity Type
Business
Look and feel

```html
<!DOCTYPE html>
<html lang="en">
<head>
<meta charset="utf-8">
<title>Lornavel — Coffee's for closers only</title>
<link rel="stylesheet" href="https://fonts.googleapis.com/css2?family=Tinos:wght@700&display=swap">
<style>
  :root {
    --card: #ffffff;
    --headline-blue: #3b5ba5;
    --closer-orange: #f6a623;
    --cup-light: #f6f6f6;
    --cup-mid: #dcdcdc;
    --cup-shade: #b4b4b4;
    --foam: #fbfaf7;
    --coffee: #9a6a3e;
  }
  * { margin: 0; padding: 0; box-sizing: border-box; }
  html, body {
    width: 1200px;
    height: 962px;
    overflow: hidden;
    background: var(--card);
  }
  .banner {
    position: relative;
    width: 1200px;
    height: 962px;
    background: var(--card);
    font-family: "Tinos", "Times New Roman", serif;
    font-weight: 700;
  }
  .headline {
    position: absolute;
    left: 24px;
    top: 34px;
    font-size: 120px;
    line-height: 1;
    color: var(--headline-blue);
    white-space: nowrap;
  }
  .subline {
    position: absolute;
    right: 14px;
    top: 214px;
    font-size: 86px;
    line-height: 1;
    color: var(--closer-orange);
    white-space: nowrap;
  }
  .coffee-cup {
    position: absolute;
    left: 20px;
    top: 290px;
    width: 480px;
    height: 520px;
  }
  .brand {
    position: absolute;
    right: 22px;
    bottom: 34px;
    display: flex;
    align-items: center;
    gap: 22px;
  }
  .brand-dot {
    width: 140px;
    height: 140px;
    background: var(--closer-orange);
    border-radius: 22px;
  }
  .brand-text {
    display: flex;
    flex-direction: column;
  }
  .brand-name {
    font-size: 92px;
    line-height: 1;
    color: var(--headline-blue);
  }
  .brand-tagline {
    font-size: 22px;
    line-height: 1.2;
    color: var(--headline-blue);
    text-align: right;
    margin-top: 4px;
  }
</style>
</head>
<body>
  <main class="banner">
    <h1 class="headline">Put that coffee down!</h1>
    <p class="subline">Coffee's for closers only</p>

    <svg class="coffee-cup" viewBox="0 0 480 520" role="img" aria-label="A white coffee mug topped with whipped cream">
      <defs>
        <linearGradient id="cupTone" x1="0" y1="0" x2="0" y2="1">
          <stop offset="0" stop-color="var(--foam)"/>
          <stop offset="0.28" stop-color="var(--coffee)"/>
          <stop offset="0.36" stop-color="var(--cup-light)"/>
          <stop offset="0.75" stop-color="var(--cup-mid)"/>
          <stop offset="1" stop-color="var(--cup-shade)"/>
        </linearGradient>
      </defs>
      <rect x="0" y="0" width="480" height="520" rx="60" fill="url(#cupTone)"/>
    </svg>

    <div class="brand">
      <span class="brand-dot" aria-hidden="true"></span>
      <div class="brand-text">
        <span class="brand-name">Lornavel</span>
        <span class="brand-tagline">business referral network</span>
      </div>
    </div>
  </main>
</body>
</html>
```